Wellness Coach/Personal trainer needs wordpress site/blog with ecommerce capable membership area

We need a WordPress design for FitPennyCoach.com. This is a blog about wellness, weight loss, and health related topics. Design logo will be provided to the winner.

A great site with a design that we would like to emulate are http://qv4.example. The design should be simple, clean, unique, fun, and distinctive. Above all, it should be highly readable and easy to navigate.

These are the specific sections/categories of the blog that should be included and incorporated into the design SEE BELOW.

Thanks in advance for your consideration
Updates

Project Deadline Extended
Reason: I have extended the deadline to evaluate more designs from other pros

Hello all, Please take a minute to review the requirements for this project and please make sure you are capable of meeting ALL the requirements. As you already know I will be making a decision very shortly on whose design I will be moving forward with, if there are any last minute submissions now is the time. Thank you for your time.

Target Market(s)

90 % women 10 % men my clients are usually professionals who value their appearance, health, longevity and time.

Industry/Entity Type

Personal Trainer

Font styles to use
Serif

Colors
886aae
ffcf3e

Requirements
Must have
• Requirements

- start losing weight today.... 555 207 9184 (first line)
- visuals/images and backgrounds to give the idea of wellness, weight loss, healthy living, etc
- navigation menu - home, who we are, what we do, who we serve, blog, contact, members area

1) slider element at top below navigation menu
2) slider element near bottom of page will have testimonials
3) contact form/inquiry form (one page)
4) will provide wellness logo (to give credibility)
5) color scheme purple, gold and white
6) membership area
7) fb, tw, youtube icons
8) footer area - In the footer, there will be smaller company logo, copyright,
disclaimer, privacy policy, terms n conditions, verse of day, and contact info, Phone: (555) 207-9184
Email: support@...
Address:
9) use dummy content/graphic as they will be replaced by real content (the winner will provide instruction on how to make changes to all text and changing graphics)
9) ecommerce enabled / newsletter signup area

```html
<!DOCTYPE html>
<html lang="en">
<head>
<meta charset="utf-8">
<title>FitPennyCoach.com</title>
<link href="https://fonts.googleapis.com/css2?family=Open+Sans:wght@400;600;700&display=swap" rel="stylesheet">
<style>
:root{
  --purple:#7a5a8e;
  --purple-dark:#5e4470;
  --purple-soft:rgba(110,78,132,.88);
  --gold:#ffcf3e;
  --beige:#f1e7da;
  --ink:#333;
  --muted:#888;
  --line:#e2dcd4;
  --footer-dark:#3a3a3a;
}
*{box-sizing:border-box;margin:0;padding:0}
html,body{width:796px;height:1200px;overflow:hidden}
body{font-family:"Open Sans",Arial,sans-serif;color:var(--ink);background:#fff;position:relative}
.site-header{height:74px;border-top:4px solid var(--purple);display:flex;align-items:center;justify-content:space-between;padding:0 92px 0 86px;border-bottom:1px solid var(--line)}
.brand{font-family:"Open Sans",Arial,sans-serif;font-weight:600;font-size:18px;color:var(--purple-dark);white-space:nowrap}
.main-nav{display:flex;gap:16px;font-size:9px;color:#666;text-transform:uppercase;letter-spacing:.3px;white-space:nowrap}
.main-nav .active{color:var(--purple)}
.hero{position:relative;height:342px;overflow:hidden}
.hero-photo{position:absolute;inset:0;background:linear-gradient(180deg,#cfd9e0 0%,#e4e9ea 52%,#7f9fae 58%,#9cb6bf 68%,#d8cdb8 76%,#c3a98a 100%)}
.hero-badge{position:absolute;left:111px;top:53px;width:254px;height:254px;border-radius:50%;background:var(--purple-soft);color:#fff;text-align:center;padding-top:58px;font-size:26px;line-height:31px;letter-spacing:1px;text-transform:uppercase}
.hero-badge .phone{display:block;margin-top:14px;font-size:24px;letter-spacing:.5px}
.hero-arrow{position:absolute;top:150px;width:26px;height:26px;border-radius:50%;background:rgba(255,255,255,.55)}
.hero-arrow svg{display:block;margin:7px auto}
.hero-arrow.prev{left:22px}.hero-arrow.next{right:22px}
.quote-band{background:var(--beige);height:127px;display:flex;align-items:center;padding:0 100px 0 112px;gap:14px}
.quote-mark{font-size:54px;color:#777;line-height:1;align-self:flex-start;margin-top:24px}
.quote-band p{font-size:10px;line-height:17px;color:#666;font-style:italic}
.content{display:flex;padding:28px 94px 0 98px;gap:30px}
.posts{width:381px}
.post{display:flex;gap:16px;height:155px}
.post-thumb{width:119px;height:112px;border:4px solid #fff;box-shadow:0 0 0 1px var(--line);flex:none}
.thumb-a{background:linear-gradient(135deg,#d9d4cc,#b9a79a)}
.thumb-b{background:linear-gradient(180deg,#bfd8ea,#8fb46a)}
.thumb-c{background:linear-gradient(180deg,#d5e1ea,#9dbf86)}
.post-meta{display:flex;justify-content:space-between;font-size:7px;color:var(--muted);margin-bottom:7px}
.post-meta span::before{content:"";display:inline-block;width:6px;height:6px;border-radius:50%;background:var(--purple);margin-right:4px;vertical-align:-1px}
.post h2{font-size:13px;font-weight:700;margin-bottom:6px}
.post p{font-size:7.5px;line-height:12px;color:#777}
.read-more{display:inline-block;margin-top:6px;font-size:8px;color:var(--ink)}
.read-more::after{content:" \25B6";color:var(--purple);font-size:6px}
.pagination{font-size:8px;color:var(--purple);margin-top:-8px;word-spacing:3px}
.sidebar{width:193px}
.widget{border:1px solid var(--line);padding:0 12px 14px;margin-bottom:26px;position:relative}
.widget-title{background:var(--purple);color:#fff;font-size:13px;font-weight:700;letter-spacing:1px;text-transform:uppercase;height:26px;line-height:26px;padding-left:26px;margin:8px -20px 12px 0;position:relative}
.widget-title::before{content:"";position:absolute;left:0;bottom:-6px;border-top:6px solid var(--purple-dark);border-left:8px solid transparent}
.field{height:20px;border:1px solid #ccc;font-size:7px;color:var(--muted);padding:5px 6px;margin:0 0 8px 20px}
.field.area{height:46px}
.btn{display:inline-block;background:#222;color:#fff;font-size:7px;padding:5px 11px;margin-left:20px;text-transform:uppercase}
.widget p{font-size:7px;line-height:11px;color:#777;margin:0 0 10px 20px}
.site-footer{position:absolute;left:0;right:0;top:1055px;height:90px;background:var(--beige);display:flex;align-items:center;padding:0 90px 0 94px;gap:50px;font-size:8px;color:#555;line-height:12px}
.foot-item{display:flex;align-items:center;gap:12px;width:200px}
.foot-item svg{flex:none}
.footer-bar{position:absolute;left:0;right:0;bottom:0;height:55px;background:var(--footer-dark);display:flex;align-items:center;justify-content:space-between;padding:0 84px 0 94px;color:#bbb;font-size:7.5px}
.footer-bar .brand{color:#ddd;font-size:16px}
.footer-links{text-align:center;line-height:12px}
.social{display:flex;gap:8px}
.social span{width:18px;height:18px;background:#888}
</style>
</head>
<body>
<header class="site-header">
  <div class="brand">FitPennyCoach.com</div>
  <nav class="main-nav"><span class="active">Home</span><span>Who We Are</span><span>What We Do</span><span>Who We Serve</span><span>Contact</span><span>Blog</span><span>Members</span></nav>
</header>

<section class="hero">
  <div class="hero-photo" role="img" aria-label="Woman meditating on a grassy beach facing the sea"></div>
  <div class="hero-badge">Start<br>Losing<br>Weight<br>Today<span class="phone">555 207 9184</span></div>
  <span class="hero-arrow prev"><svg width="8" height="12" viewBox="0 0 8 12"><path d="M7 1L2 6l5 5" stroke="#fff" stroke-width="2" fill="none"/></svg></span>
  <span class="hero-arrow next"><svg width="8" height="12" viewBox="0 0 8 12"><path d="M1 1l5 5-5 5" stroke="#fff" stroke-width="2" fill="none"/></svg></span>
</section>

<section class="quote-band">
  <span class="quote-mark">&ldquo;</span>
  <p>Lorem ipsum dolor sit amet, consectetuer adipiscing elit. Aenean commodo ligula eget dolor. Aenean massa. Cum sociis natoque penatibus et magnis dis parturient montes, nascetur ridiculus mus. Donec quam felis, ultricies nec, pellentesque eu, pretium.</p>
</section>

<main class="content">
  <div class="posts">
    <article class="post">
      <div class="post-thumb thumb-a" role="img" aria-label="Woman stretching on a mat"></div>
      <div>
        <div class="post-meta"><span>Admin | May 28th, 2013</span><span>10 Comments</span></div>
        <h2>Consectetuer adipiscing elit</h2>
        <p>Lorem ipsum dolor sit amet, consectetuer adipiscing elit. Aenean commodo ligula eget dolor. Aenean massa. Cum sociis natoque penatibus et magnis dis parturient montes, nascetur ridiculus mus. Donec quam felis, ultricies nec.</p>
        <a class="read-more">Read More</a>
      </div>
    </article>
    <article class="post">
      <div class="post-thumb thumb-b" role="img" aria-label="Woman exercising outdoors on grass"></div>
      <div>
        <div class="post-meta"><span>Admin | May 28th, 2013</span><span>10 Comments</span></div>
        <h2>Consectetuer adipiscing elit</h2>
        <p>Lorem ipsum dolor sit amet, consectetuer adipiscing elit. Aenean commodo ligula eget dolor. Aenean massa. Cum sociis natoque penatibus et magnis dis parturient montes, nascetur ridiculus mus. Donec quam felis, ultricies nec.</p>
        <a class="read-more">Read More</a>
      </div>
    </article>
    <article class="post">
      <div class="post-thumb thumb-c" role="img" aria-label="Woman in a yoga pose in a meadow"></div>
      <div>
        <div class="post-meta"><span>Admin | May 28th, 2013</span><span>10 Comments</span></div>
        <h2>Consectetuer adipiscing elit</h2>
        <p>Lorem ipsum dolor sit amet, consectetuer adipiscing elit. Aenean commodo ligula eget dolor. Aenean massa. Cum sociis natoque penatibus et magnis dis parturient montes, nascetur ridiculus mus. Donec quam felis, ultricies nec.</p>
        <a class="read-more">Read More</a>
      </div>
    </article>
    <div class="pagination">1 2 3 4 of 15 Next</div>
  </div>

  <aside class="sidebar">
    <section class="widget">
      <h3 class="widget-title">Inquiry</h3>
      <div class="field">Name</div>
      <div class="field">Phone</div>
      <div class="field">Email</div>
      <div class="field area">Message</div>
      <span class="btn">Send</span>
    </section>
    <section class="widget">
      <h3 class="widget-title">Membership</h3>
      <p>Lorem ipsum dolor sit amet, consectetuer adipiscing elit. Aenean commodo ligula eget dolor. Aenean massa. Cum sociis natoque penatibus et magnis dis parturient.</p>
      <span class="btn">Join Today</span>
    </section>
  </aside>
</main>

<footer class="site-footer">
  <div class="foot-item">
    <svg width="16" height="22" viewBox="0 0 16 22"><path d="M8 21S1 12 1 8a7 7 0 0 1 14 0c0 4-7 13-7 13z" fill="#555"/><circle cx="8" cy="8" r="2.6" fill="#f1e7da"/></svg>
    <span>Lorem ipsum dolor sit amet, consectetuer adipiscing elit</span>
  </div>
  <div class="foot-item">
    <svg width="18" height="18" viewBox="0 0 18 18"><path d="M4 1l3 4-2 2c1 2 3 4 6 6l2-2 4 3-2 3C8 17 1 10 1 3z" fill="#555"/></svg>
    <span>Call Us :<br>(555) 207-9184</span>
  </div>
  <div class="foot-item">
    <svg width="22" height="16" viewBox="0 0 22 16"><rect x="1" y="1" width="20" height="14" fill="#555"/><path d="M1 1l10 8 10-8" stroke="#f1e7da" stroke-width="1.5" fill="none"/></svg>
    <span>Email :<br>support@fitpennycoach.com</span>
  </div>
</footer>
<div class="footer-bar">
  <div class="brand">FitPennyCoach.com</div>
  <div class="footer-links">Copyright | Disclaimer | Privacy policy<br>Terms n conditions | Verse of day</div>
  <div class="social"><span></span><span></span><span></span></div>
</div>
</body>
</html>
```